Heron Loan Partners Business Card

We need a business card design for our mortgage servicing company. In addition to servicing the loans of homeowners, we help homeowners with purchasing their homes and any mortgage refinancing. We would like to see designs that use the colors in the logo attached below (gold-ish yellow and navy blue), and any other design you deem fit! The design should communicate a simpler life with smart mortgages provided by Heron.

```html
<!DOCTYPE html>
<html lang="en">
<head>
<meta charset="UTF-8">
<title>Heron Loan Partners Business Card</title>
<link href="https://fonts.googleapis.com/css2?family=Open+Sans:wght@400;600;700&display=swap" rel="stylesheet">
<style>
  :root {
    --navy: #272052;
    --gold: #e1b13c;
    --white: #ffffff;
    --ink: #1b1b1b;
    --stage: #232323;
  }
  * { margin: 0; padding: 0; box-sizing: border-box; }
  html, body { width: 1200px; height: 780px; overflow: hidden; background: var(--stage); }
  body { position: relative; font-family: "Open Sans", Arial, sans-serif; }

  .card {
    position: absolute;
    width: 520px;
    height: 298px;
    border-radius: 18px;
    border: 3px solid var(--gold);
    overflow: hidden;
  }
  .card-back { left: 40px; top: 110px; background: var(--navy); }
  .card-front { left: 640px; top: 372px; background: var(--white); }

  .brand-name {
    position: absolute;
    font-weight: 700;
    color: var(--gold);
    letter-spacing: 0.5px;
    white-space: nowrap;
  }
  .card-back .brand-name { left: 0; right: 0; top: 124px; text-align: center; font-size: 34px; }
  .card-front .brand-name { left: 18px; width: 230px; top: 120px; text-align: center; font-size: 22px; }

  .divider { position: absolute; left: 262px; top: 48px; width: 1.5px; height: 152px; background: var(--ink); }

  .contact { position: absolute; left: 284px; top: 40px; color: var(--ink); }
  .person-name { font-size: 22px; font-weight: 700; line-height: 1.1; }
  .person-name .first { color: var(--gold); }
  .person-name .last { color: var(--navy); }
  .person-title { font-size: 12.5px; font-weight: 600; margin-top: 2px; }
  .address { font-size: 12.5px; line-height: 1.35; margin-top: 14px; }
  .links { list-style: none; margin-top: 12px; font-size: 12.5px; line-height: 1.55; }
  .links li { display: flex; align-items: center; gap: 8px; }
  .links svg { width: 11px; height: 11px; flex: none; }

  .bands { position: absolute; left: 0; bottom: 0; width: 100%; height: 80px; }
</style>
</head>
<body>
  <section class="card card-back">
    <p class="brand-name">Heron Loan Partners</p>
  </section>

  <section class="card card-front">
    <p class="brand-name">Heron Loan Partners</p>
    <div class="divider"></div>
    <div class="contact">
      <h1 class="person-name"><span class="first">Lena</span> <span class="last">Varkova</span></h1>
      <p class="person-title">Managing Director</p>
      <p class="address">418 Lakeside Ave. Suite<br>300 Denton, TX 76201</p>
      <ul class="links">
        <li><svg viewBox="0 0 12 12"><path fill="#e1b13c" d="M2.5 1l2 2-1 1.3c.7 1.5 1.7 2.5 3.2 3.2L8 6.5l2 2-1.3 1.8C5 10 2 7 1.7 2.3z"/></svg>(940) 555-0184</li>
        <li><svg viewBox="0 0 12 12"><rect x="1" y="2.5" width="10" height="7" rx="1" fill="#e1b13c"/><path d="M1.5 3l4.5 3.5L10.5 3" stroke="#fff" stroke-width="1" fill="none"/></svg>info@website.com</li>
        <li><svg viewBox="0 0 12 12"><circle cx="6" cy="6" r="5" fill="#e1b13c"/><path d="M1 6h10M6 1c2 2 2 8 0 10M6 1c-2 2-2 8 0 10" stroke="#fff" stroke-width=".8" fill="none"/></svg>www.website.com</li>
      </ul>
    </div>
    <svg class="bands" viewBox="0 0 520 80" preserveAspectRatio="none">
      <path d="M330 30 L520 30 L520 80 L300 80 Q312 30 330 30 Z" fill="var(--navy)"/>
      <path d="M0 52 L300 52 Q292 64 288 68 L0 68 Z" fill="var(--gold)"/>
    </svg>
  </section>
</body>
</html>
```